Refresh of far from plain IT company website

Our web site is starting to show it's age. You can see the existing site here: www.plumbwick.net. As a growing company we want to come across as a dynamic collection of IT experts.

We want to update the design so are open to any colour palette and look, but want to retain our current table logo. We use the logo on our business cards but with a white background - see the attached file, so you don't need to keep the brown or the green.

The design should consider the range of browsers that will be looking at the site - so please show how it will look on a wide screen laptop and a 768x1024 tablet.

We want to add some pages about our team and their skills, probably with photos of each person on the team.

This is an uncoded project - the PSD files of the design is required, not coding.
Updates

Thanks everyone for the submissions so far.  It's a holiday day in the UK today but we will get some feedback on the designs so far out to you.

Target Market(s)

Architects and other creative types looking for IT support

Industry/Entity Type

Business

Font styles to use
Serif
Sans Serif

Requirements
Must have
• Must look good on a laptop and an iPad.

```html
<!DOCTYPE html>
<html lang="en">
<head>
<meta charset="utf-8">
<title>Plumbwick – far from plain IT company</title>
<link href="https://fonts.googleapis.com/css2?family=Open+Sans:wght@400;600;700&display=swap" rel="stylesheet">
<style>
:root{
  --maroon:#7b1d48;
  --maroon-dark:#5e1436;
  --gold:#e0a81b;
  --sage:#6d7769;
  --sage-dark:#4f574c;
  --ink:#333;
  --muted:#666;
  --line:#dcdcdc;
  --nav:#ececec;
  --footer:#e6e6e6;
  --base:#2f2f2f;
  --white:#fff;
}
*{box-sizing:border-box;margin:0;padding:0}
html,body{width:835px;height:1200px;overflow:hidden;background:var(--white)}
body{font-family:"Open Sans",Arial,sans-serif;color:var(--ink);font-size:10px;line-height:1.5;position:relative}
a{color:inherit;text-decoration:none}
.wrap{width:715px;margin:0 auto;position:relative}

/* header */
.site-header{height:80px}
.brand{position:absolute;left:0;top:24px;display:flex;align-items:center;gap:10px}
.brand-mark{width:28px;height:28px;background:var(--gold)}
.brand-name{font-size:26px;font-weight:700;color:var(--maroon);letter-spacing:-.5px}
.search{position:absolute;right:0;top:28px;display:flex}
.search input{width:130px;height:24px;border:1px solid var(--line);padding:0 8px;font:inherit;color:#999}
.search button{width:26px;height:24px;border:0;background:var(--maroon)}

/* nav */
.main-nav{height:20px;background:var(--nav);border-top:1px solid var(--line);border-bottom:1px solid var(--line)}
.main-nav ul{list-style:none;display:flex;height:100%}
.main-nav li{padding:0 16px;font-size:10px;line-height:18px;color:#555}
.main-nav li.active{background:var(--maroon);color:var(--white)}

/* hero */
.hero{height:270px;position:relative;background:linear-gradient(110deg,#9aa0a6 0%,#cfd4d8 35%,#5b6470 70%,#2d333c 100%)}
.hero-caption{position:absolute;left:60px;bottom:32px;width:230px;background:rgba(40,40,40,.75);color:var(--white);padding:8px 12px}
.hero-caption h2{font-size:13px;font-weight:600}
.hero-caption p{font-size:8px;color:#ddd}
.hero-arrow{position:absolute;top:125px;width:16px;height:16px;border-radius:50%;background:rgba(255,255,255,.6)}
.hero-arrow.prev{left:10px}.hero-arrow.next{right:10px}

/* welcome */
.welcome{height:140px;background:var(--sage);color:var(--white)}
.welcome .wrap{padding-top:22px;display:flex;justify-content:space-between}
.welcome h2{font-size:17px;font-weight:600;margin-bottom:4px}
.welcome p{width:480px;font-size:9.5px;color:#eef0ec}
.remote h3{font-size:11px;font-weight:600;margin:6px 0 8px}
.remote form{display:flex}
.remote input{width:100px;height:22px;border:0;padding:0 6px;font:inherit}
.remote button{width:30px;height:22px;border:0;background:var(--gold)}

/* columns */
.columns{display:flex;justify-content:space-between;padding-top:22px;height:380px}
.col{width:220px}
.col h3{font-size:12px;font-weight:700;margin-bottom:8px}
.col p{font-size:8.5px;color:var(--muted);margin-bottom:8px}
.photo{background:linear-gradient(135deg,#d9d3cc,#8a8f96)}
.team-photo{height:90px;margin-bottom:8px}
.btn{display:inline-block;background:var(--maroon);color:var(--white);font-size:8.5px;padding:5px 14px}
.services{list-style:none;margin-bottom:12px}
.services li{font-size:9px;padding:4px 0 4px 12px;border-bottom:1px solid #eee;position:relative}
.services li::before{content:"";position:absolute;left:0;top:9px;border:3px solid transparent;border-left:4px solid var(--maroon)}
.news-item{display:flex;gap:8px;margin-bottom:10px}
.news-thumb{width:50px;height:40px;flex:none;background:linear-gradient(135deg,#2c5a8a,#7fb2d8)}
.news-item p{font-size:8px;margin:0}
.news-item strong{display:block;color:var(--maroon);font-size:8.5px}

/* partners */
.partners{height:80px;background:var(--sage-dark)}
.partners .wrap{display:flex;align-items:center;height:100%;gap:38px}
.partners h3{color:var(--white);font-size:12px;font-weight:600;width:90px}
.partner-badge{width:100px;height:26px;background:rgba(255,255,255,.85)}

/* footer */
.site-footer{height:165px;background:var(--footer);padding-top:18px}
.site-footer .wrap{display:flex;justify-content:space-between}
.footer-col h4{font-size:11px;font-weight:600;margin-bottom:8px}
.map{width:150px;height:60px;background:linear-gradient(135deg,#e8e4d8,#c9d6c0);margin-bottom:6px}
.footer-col p{font-size:8px;color:var(--muted)}
.footer-links{list-style:none;font-size:8.5px;color:#555}
.footer-links li{padding:1px 0}
.social{list-style:none;font-size:8.5px;color:#555}
.social li{display:flex;align-items:center;gap:6px;margin-bottom:5px}
.social span{width:14px;height:14px;background:var(--maroon)}

/* base */
.base-bar{height:65px;background:var(--base);color:#bbb;font-size:8.5px}
.base-bar .wrap{display:flex;justify-content:space-between;padding-top:22px}
.base-bar nav{display:flex;gap:20px}
</style>
</head>
<body>
<header class="site-header wrap">
  <a class="brand" href="#"><span class="brand-mark"></span><span class="brand-name">plumbwick</span></a>
  <form class="search"><input value="Search"><button type="button" aria-label="Search"></button></form>
</header>

<nav class="main-nav"><div class="wrap"><ul>
  <li class="active">Home</li><li>About us</li><li>What we do</li><li>News blog</li><li>Articles</li><li>Clients</li><li>Partners</li><li>Contact Us</li>
</ul></div></nav>

<section class="hero" role="img" aria-label="Businessman touching a glowing digital interface">
  <span class="hero-arrow prev"></span><span class="hero-arrow next"></span>
  <div class="hero-caption">
    <h2>Cloud Computing</h2>
    <p>Secure hosted platforms that keep your studio files safe, shared and ready wherever your team works.</p>
  </div>
</section>

<section class="welcome"><div class="wrap">
  <div>
    <h2>Welcome</h2>
    <p>Plumbwick was established with a specific aim: to consistently deliver an advanced and comprehensive IT service for ambitious growing companies across all industry sectors.</p>
  </div>
  <div class="remote">
    <h3>Remote</h3>
    <form><input value="Session ID"><button type="button" aria-label="Connect"></button></form>
  </div>
</div></section>

<main class="columns wrap">
  <div class="col">
    <h3>Who We Are?</h3>
    <div class="photo team-photo" role="img" aria-label="Team of smiling IT consultants"></div>
    <p>Plumbwick was established with a specific aim: to consistently deliver an advanced and comprehensive IT service for ambitious growing companies across many industry sectors. We aim to provide the very best in service and support, and to anticipate growth through the effective and skilled use of modern IT systems.</p>
    <a class="btn" href="#">Read More</a>
  </div>
  <div class="col">
    <h3>What We Do?</h3>
    <p>Plumbwick offer a wide range of services tailored to meet our clients' business needs. We aim to deliver world-class support and strategic advice, backed up by an effective on-site presence. Our core business is focused on architecture practices and creative companies with sophisticated and fast changing IT requirements.</p>
    <ul class="services"><li>Support</li><li>Consultancy</li><li>CAD Services</li><li>Hosting</li><li>Development</li></ul>
    <a class="btn" href="#">Read More</a>
  </div>
  <div class="col">
    <h3>Latest News</h3>
    <div class="news-item"><div class="news-thumb" role="img" aria-label="News thumbnail"></div><p><strong>12 May 2014</strong>New backup service launched for studio teams.</p></div>
    <div class="news-item"><div class="news-thumb" role="img" aria-label="News thumbnail"></div><p><strong>28 Apr 2014</strong>Moving your practice to the cloud made simple.</p></div>
    <div class="news-item"><div class="news-thumb" role="img" aria-label="News thumbnail"></div><p><strong>09 Apr 2014</strong>Tips for faster rendering on shared workstations.</p></div>
    <a class="btn" href="#">Read More</a>
  </div>
</main>

<section class="partners"><div class="wrap">
  <h3>Our Partners</h3>
  <span class="partner-badge"></span><span class="partner-badge"></span><span class="partner-badge"></span><span class="partner-badge"></span>
</div></section>

<footer class="site-footer"><div class="wrap">
  <div class="footer-col">
    <h4>Get In Touch</h4>
    <div class="map" role="img" aria-label="Street map of office location"></div>
    <p>12 Orchard Lane, Kestwell, KW4 7TR</p>
    <p>Phone: 01632 960 418</p>
    <p>hello@plumbwick.net</p>
  </div>
  <div class="footer-col">
    <h4>Get in Touch</h4>
    <ul class="footer-links"><li>Home</li><li>About Us</li><li>What we do</li><li>News blog</li><li>Articles</li><li>Clients</li><li>Partners</li></ul>
  </div>
  <div class="footer-col">
    <h4>Contact Us</h4>
    <ul class="social"><li><span></span>Social page</li><li><span></span>Updates</li><li><span></span>Network</li><li><span></span>Circles</li></ul>
  </div>
</div></footer>

<div class="base-bar"><div class="wrap">
  <nav><a>Contact</a><a>Support</a><a>Terms</a><a>Sitemap</a><a>Privacy &amp; Policy</a></nav>
  <span>Copyright © 2014 Plumbwick. All rights reserved.</span>
</div></div>
</body>
</html>
```